HearthMile business card and stationary design

We are looking for a simple yet elegant design for our mortgage company business card and stationary.

The card should include:
Name (Marcus Pell)
Title (CEO)
Phone Number (415-555-0182)
Address (48 Birchwell Court, Suite 314, Ashbrook Vale, OR 97999)
Email (email@hearthmile.example)
"NMLS" i.e. (NMLS 61947)
"Company NMLS" (Company NMLS 274615)

Contact Information for Business Card

See above

```html
<!DOCTYPE html>
<html lang="en">
<head>
<meta charset="utf-8">
<title>HearthMile Business Card</title>
<link rel="stylesheet" href="https://fonts.googleapis.com/css2?family=Figtree:wght@400;500;600&display=swap">
<style>
  :root {
    --backdrop: #8e8e8e;
    --navy: #131e29;
    --navy-soft: #1b2a38;
    --blue: #1a94d6;
    --ink: #1d2630;
    --paper: #e9eaec;
  }
  * { box-sizing: border-box; margin: 0; padding: 0; }
  html, body {
    width: 1200px;
    height: 781px;
    overflow: hidden;
  }
  body {
    background: var(--backdrop);
    font-family: "Figtree", sans-serif;
    color: var(--ink);
    position: relative;
  }
  .card {
    position: absolute;
    left: 358px;
    width: 452px;
    height: 251px;
    overflow: hidden;
  }
  .card-front {
    top: 103px;
    background: radial-gradient(ellipse at 50% 110%, var(--navy-soft) 0%, var(--navy) 65%);
    display: flex;
    align-items: center;
    justify-content: center;
  }
  .front-wordmark {
    font-size: 54px;
    font-weight: 500;
    color: var(--blue);
    letter-spacing: -0.5px;
    margin-top: 0;
  }
  .card-back {
    top: 408px;
    background: var(--paper);
  }
  .back-wordmark {
    position: absolute;
    left: 50px;
    top: 42px;
    font-size: 33px;
    font-weight: 500;
    color: var(--blue);
    letter-spacing: -0.3px;
  }
  .contact {
    position: absolute;
    left: 264px;
    top: 48px;
    width: 182px;
  }
  .person-name {
    font-size: 16.5px;
    font-weight: 600;
    letter-spacing: 1.3px;
    color: var(--blue);
    text-transform: uppercase;
    line-height: 1;
  }
  .person-title {
    font-size: 13px;
    margin-top: 3px;
    line-height: 1.1;
  }
  .divider {
    width: 18px;
    height: 1px;
    background: var(--blue);
    margin: 12px 0 11px;
  }
  .line-item {
    display: flex;
    align-items: center;
    gap: 6px;
    font-size: 12.5px;
    line-height: 19px;
  }
  .line-item svg { flex: none; }
  .address {
    font-size: 12.5px;
    line-height: 18px;
    margin-top: 7px;
  }
  .licences {
    font-size: 10px;
    line-height: 14px;
    margin-top: 7px;
  }
  .band {
    position: absolute;
    left: 0;
    bottom: 0;
    height: 8px;
    width: 100%;
    display: flex;
  }
  .band-dark { width: 242px; background: var(--navy); }
  .band-blue { flex: 1; background: var(--blue); }
</style>
</head>
<body>
  <section class="card card-front">
    <div class="front-wordmark">HearthMile</div>
  </section>

  <section class="card card-back">
    <div class="back-wordmark">HearthMile</div>

    <div class="contact">
      <div class="person-name">Marcus Pell</div>
      <div class="person-title">CEO</div>
      <div class="divider"></div>

      <div class="line-item">
        <svg width="12" height="12" viewBox="0 0 24 24" fill="none" stroke="#1a94d6" stroke-width="2" stroke-linejoin="round">
          <path d="M5 3h4l2 5-2.5 1.5a11 11 0 0 0 6 6L16 13l5 2v4a2 2 0 0 1-2 2A16 16 0 0 1 3 5a2 2 0 0 1 2-2z"/>
        </svg>
        <span>415-555-0182</span>
      </div>
      <div class="line-item">
        <svg width="13" height="11" viewBox="0 0 26 20" fill="none" stroke="#1a94d6" stroke-width="2" stroke-linejoin="round">
          <rect x="1" y="1" width="24" height="18"/>
          <path d="M1 1l12 10L25 1"/>
        </svg>
        <span>email@hearthmile.example</span>
      </div>

      <div class="address">48 Birchwell Court, Suite 314,<br>Ashbrook Vale, OR 97999</div>

      <div class="licences">NMLS 61947<br>Company NMLS 274615</div>
    </div>

    <div class="band">
      <div class="band-dark"></div>
      <div class="band-blue"></div>
    </div>
  </section>
</body>
</html>
```